Harborline Renewal Business Card Design

Professional and clean design. The design colors should flow with the logo. Two-sided card with the website on the back which is:

www.HarborlineRenewal.example.

"Specializing in Water Damage Restoration"

On the front I need the name, email, phone, and logo.

Name: Darnell Quisby
Email: Darnell@HarborlineRenewal.example
Phone: 555-318-2046 for now

I only have the Preview and Thumbnail right now but should have the source files uploaded within a day or two.

Target Market(s)

Flood victims, home owners with water damage from busted pipes etc...

Industry/Entity Type

Business

Contact Information for Business Card

Name: Darnell Quisby

Font styles to use
Serif
Sans Serif

Requirements
Must have
• Business Card Details Info

```html
<!DOCTYPE html>
<html lang="en">
<head>
<meta charset="utf-8">
<title>Harborline Renewal Business Card</title>
<link rel="stylesheet" href="https://fonts.googleapis.com/css2?family=Cinzel:wght@400;600&family=Open+Sans:wght@400&display=swap">
<style>
  :root {
    --blue-deep: #2b93d4;
    --blue-light: #5cc0ef;
    --ink: #1f1f1f;
    --ink-soft: #2a2a2a;
    --paper: #ffffff;
    --stage: #ece8e2;
    --edge: #3a3a3a;
  }
  * { box-sizing: border-box; margin: 0; padding: 0; }
  html, body { width: 1200px; height: 1187px; overflow: hidden; }
  body { background: var(--stage); position: relative; font-family: "Open Sans", sans-serif; }

  .card {
    position: absolute;
    width: 906px; height: 518px;
    background: var(--paper);
    border: 1.5px solid var(--edge);
    border-radius: 40px;
    overflow: hidden;
  }
  .card--front { left: 236px; top: 58px; }
  .card--back { left: 56px; top: 641px; }

  .card__waves { position: absolute; inset: 0; width: 100%; height: 100%; }

  .mark-dot {
    position: absolute;
    border-radius: 50%;
    background: var(--blue-light);
  }
  .card--front .mark-dot { width: 100px; height: 100px; left: 403px; top: 18px; }
  .card--back .mark-dot { width: 140px; height: 140px; left: 383px; top: 74px; }

  .wordmark {
    position: absolute; left: 0; right: 0;
    text-align: center;
    font-family: "Cinzel", serif;
    font-weight: 600;
    color: var(--blue-deep);
    line-height: 1;
  }
  .wordmark__main { display: block; letter-spacing: 2px; }
  .wordmark__sub { display: block; letter-spacing: 8px; }
  .card--front .wordmark { top: 168px; }
  .card--front .wordmark__main { font-size: 54px; }
  .card--front .wordmark__sub { font-size: 23px; margin-top: 6px; }
  .card--back .wordmark { top: 250px; }
  .card--back .wordmark__main { font-size: 66px; }
  .card--back .wordmark__sub { font-size: 29px; margin-top: 8px; }

  .holder {
    position: absolute; left: 0; right: 0; top: 282px;
    text-align: center;
    font-family: "Cinzel", serif;
    font-size: 25px;
    font-weight: 600;
    color: var(--blue-deep);
  }
  .holder__title { color: var(--ink-soft); font-weight: 400; }

  .contact {
    position: absolute; left: 0; right: 0;
    display: flex; justify-content: center; align-items: center; gap: 28px;
    font-size: 21px; color: var(--ink);
  }
  .contact--phone { top: 390px; }
  .contact--web { top: 425px; }
  .contact__item { display: inline-flex; align-items: center; gap: 8px; }
  .contact__icon { width: 18px; height: 18px; }

  .tagline {
    position: absolute; left: 0; right: 0; top: 468px;
    text-align: center;
    font-family: "Cinzel", serif;
    font-size: 23px;
    letter-spacing: 1px;
    color: var(--ink-soft);
  }

  .site {
    position: absolute; left: 0; right: 0; top: 380px;
    text-align: center;
    font-size: 29px;
    letter-spacing: 1.5px;
    color: var(--ink);
  }
</style>
</head>
<body>

<section class="card card--front" aria-label="Card front">
  <svg class="card__waves" viewBox="0 0 906 518" aria-hidden="true">
    <path d="M0 282 C260 370 620 390 906 288 L906 518 L0 518 Z" fill="var(--blue-light)"/>
    <path d="M0 232 C210 320 500 352 742 346 C500 356 220 320 0 266 Z" fill="var(--blue-deep)"/>
  </svg>
  <span class="mark-dot" aria-hidden="true"></span>
  <h1 class="wordmark">
    <span class="wordmark__main">HARBORLINE</span>
    <span class="wordmark__sub">RENEWAL</span>
  </h1>
  <p class="holder">Darnell Quisby, <span class="holder__title">Title</span></p>
  <p class="contact contact--phone">
    <span class="contact__item">
      <svg class="contact__icon" viewBox="0 0 24 24" aria-hidden="true"><path d="M6.6 10.8a15 15 0 0 0 6.6 6.6l2.2-2.2a1 1 0 0 1 1-.25 11.4 11.4 0 0 0 3.6.57 1 1 0 0 1 1 1V20a1 1 0 0 1-1 1A17 17 0 0 1 3 4a1 1 0 0 1 1-1h3.5a1 1 0 0 1 1 1c0 1.25.2 2.45.57 3.57a1 1 0 0 1-.25 1z" fill="var(--ink)"/></svg>
      555-318-2046
    </span>
  </p>
  <p class="contact contact--web">
    <span class="contact__item">
      <svg class="contact__icon" viewBox="0 0 24 24" aria-hidden="true"><path d="M3 9l9-6 9 6v11H3z" fill="var(--ink)"/><path d="M3 9l9 6 9-6" fill="none" stroke="var(--paper)" stroke-width="1.8"/></svg>
      Darnell@HarborlineRenewal.example
    </span>
    <span class="contact__item">
      <svg class="contact__icon" viewBox="0 0 24 24" aria-hidden="true"><circle cx="12" cy="12" r="9.5" fill="none" stroke="var(--ink)" stroke-width="2"/><ellipse cx="12" cy="12" rx="4" ry="9.5" fill="none" stroke="var(--ink)" stroke-width="1.6"/><path d="M2.5 12h19M4.5 7h15M4.5 17h15" stroke="var(--ink)" stroke-width="1.4"/></svg>
      www.HarborlineRenewal.example
    </span>
  </p>
  <p class="tagline">Specializing in Water Damage Restoration</p>
</section>

<section class="card card--back" aria-label="Card back">
  <span class="mark-dot" aria-hidden="true"></span>
  <h2 class="wordmark">
    <span class="wordmark__main">HARBORLINE</span>
    <span class="wordmark__sub">RENEWAL</span>
  </h2>
  <p class="site">www.HarborlineRenewal.example</p>
</section>

</body>
</html>
```